Printer Cartridges Supplier Namecard

Attached is my company logo and the design of my current namecard. I would like to have a more special look for it. Can have a little cuteness too rather than those normal standard feel. I'm a supplier mainly dealing with original and compatible printer toner cartridges, some other products like paper supplies as well.

Target Market(s)

Companies, businesses, corporates

Industry/Entity Type

It Company

Contact Information for Business Card

Logo, name, contact, address, supplies and maybe a slogan

Colors
85cae6
33a6d7
3176b5
0255a3
0792cd
85abd2

Requirements
Must have
• Logo, name, contact and address basic details.
• Must include some pictures, not just rearrange what I'm currently having.
Nice to have
• Be creative and bold, a diiferent traditional feel.

```html
<!DOCTYPE html>
<html lang="en">
<head>
<meta charset="utf-8">
<title>pressdot.sg namecard</title>
<link href="https://fonts.googleapis.com/css2?family=Quicksand:wght@400;500;600;700&display=swap" rel="stylesheet">
<style>
  :root {
    --bg: #4a4540;
    --card: #1c1c1e;
    --card-edge: #232325;
    --blue: #3176b5;
    --blue-bright: #33a6d7;
    --white: #f2f2f2;
    --grey: #c9c9c9;
  }
  * { margin: 0; padding: 0; box-sizing: border-box; }
  html, body { width: 1200px; height: 930px; overflow: hidden; }
  body {
    background: var(--bg);
    font-family: "Quicksand", sans-serif;
    color: var(--white);
    position: relative;
  }
  .card {
    position: absolute;
    left: 250px;
    width: 700px;
    height: 400px;
    border-radius: 16px;
    background: radial-gradient(circle at 60% 35%, var(--card-edge), var(--card) 70%);
    overflow: hidden;
  }
  .card--front { top: 45px; }
  .card--back { top: 485px; }

  .brand { position: absolute; display: flex; flex-direction: column; }
  .brand__row { display: flex; align-items: center; gap: 12px; }
  .brand__mark { width: 22px; height: 22px; background: var(--blue); border-radius: 4px; }
  .brand__name { font-weight: 600; font-size: 62px; line-height: 1; color: var(--white); letter-spacing: -1px; }
  .brand__tagline { font-size: 11px; color: var(--white); margin-left: 36px; margin-top: 4px; }

  .card--front .brand { left: 170px; top: 110px; }

  .services { position: absolute; top: 265px; display: flex; align-items: center; }
  .services__list { list-style: none; font-size: 17px; font-weight: 500; line-height: 1.45; }
  .services__list li::before {
    content: ""; display: inline-block; width: 8px; height: 8px;
    border-radius: 50%; background: var(--blue); margin-right: 10px; vertical-align: middle;
  }
  .services__divider { width: 1px; height: 52px; background: var(--grey); margin: 0 32px; }
  .card--front .services { left: 110px; }

  .card--back .brand { left: 40px; top: 150px; }
  .card--back .brand__name { font-size: 54px; }
  .card--back .divider {
    position: absolute; left: 395px; top: 60px; width: 1px; height: 165px; background: var(--grey);
  }
  .contact { position: absolute; left: 420px; top: 55px; font-size: 14px; line-height: 1.4; }
  .contact__name { font-size: 28px; font-weight: 600; color: var(--blue-bright); line-height: 1.1; }
  .contact__role { font-size: 15px; }
  .contact__hp { color: var(--white); }
  .contact__hp span { color: var(--blue-bright); font-weight: 600; }
  .contact__line { display: flex; align-items: center; gap: 8px; }
  .contact__line svg { width: 12px; height: 12px; flex: none; }
  .contact__address { margin-top: 4px; }

  .swoosh { position: absolute; left: 0; bottom: 0; width: 700px; height: 400px; }
  .products { position: absolute; bottom: 70px; left: 220px; display: flex; gap: 24px; align-items: flex-end; }
  .product { border-radius: 6px; }
  .product--paper { width: 90px; height: 50px; background: linear-gradient(#f4f6f8, #c9d3dc); }
  .product--printer { width: 80px; height: 70px; background: linear-gradient(#e6e8ea, #9aa1a8); }
  .product--ink { width: 85px; height: 45px; background: linear-gradient(90deg, #2fb1e0, #d9338c, #f2d32a, #222); }
</style>
</head>
<body>

<section class="card card--front">
  <div class="brand">
    <div class="brand__row">
      <span class="brand__mark"></span>
      <span class="brand__name">pressdot.sg</span>
    </div>
    <span class="brand__tagline">Compatible printer ink and toner solutions</span>
  </div>
  <div class="services">
    <ul class="services__list">
      <li>Printer Ink &amp; Toner Cartridges</li>
      <li>Original Printer Cartridges</li>
    </ul>
    <span class="services__divider"></span>
    <ul class="services__list">
      <li>Paper Products</li>
      <li>Printer Maintainence &amp; Repair</li>
    </ul>
  </div>
</section>

<section class="card card--back">
  <svg class="swoosh" viewBox="0 0 700 400" aria-hidden="true">
    <path d="M0 385 L440 300 C480 292 490 250 540 240 L700 208 L700 400 L0 400 Z" fill="var(--blue)"/>
    <path d="M0 372 L440 290 C478 283 488 244 536 233 L700 200" fill="none" stroke="var(--blue)" stroke-width="3"/>
    <path d="M0 392 L700 262" fill="none" stroke="var(--card)" stroke-width="4"/>
  </svg>

  <div class="brand">
    <div class="brand__row">
      <span class="brand__mark"></span>
      <span class="brand__name">pressdot.sg</span>
    </div>
    <span class="brand__tagline">Compatible printer ink and toner solutions</span>
  </div>

  <span class="divider"></span>

  <div class="contact">
    <div class="contact__name">Mira Tan</div>
    <div class="contact__role">Sales Executive</div>
    <div class="contact__hp"><span>HP</span> 9000 1234</div>
    <div class="contact__line">
      <svg viewBox="0 0 12 12"><path d="M2 1 L4.5 1 L5.5 3.5 L4 4.5 C5 6.5 5.5 7 7.5 8 L8.5 6.5 L11 7.5 L11 10 C6 11 1 6 2 1 Z" fill="var(--blue-bright)"/></svg>
      310-555-0142
    </div>
    <div class="contact__line">
      <svg viewBox="0 0 12 12"><rect x="1" y="2.5" width="10" height="7" rx="1" fill="none" stroke="var(--blue-bright)"/><path d="M1 3 L6 7 L11 3" fill="none" stroke="var(--blue-bright)"/></svg>
      mira@pressdot.sg
    </div>
    <div class="contact__line">
      <svg viewBox="0 0 12 12"><circle cx="6" cy="6" r="5" fill="none" stroke="var(--blue-bright)"/><path d="M1 6 H11 M6 1 C3 4 3 8 6 11 C9 8 9 4 6 1" fill="none" stroke="var(--blue-bright)"/></svg>
      www.pressdot.sg
    </div>
    <div class="contact__address">12A Harbourview Lane<br>#04-118 Singapore 500123</div>
  </div>

  <div class="products">
    <div class="product product--paper" role="img" aria-label="Stack of copy paper reams"></div>
    <div class="product product--printer" role="img" aria-label="Office multifunction printer"></div>
    <div class="product product--ink" role="img" aria-label="Set of cyan, magenta, yellow and black ink cartridges"></div>
  </div>
</section>

</body>
</html>
```